Carpet cleaning company focused on high quality needs business cards

We are a growing company that just merged with another company and need to design a new business card. We do both residential as well as commercial cleaning. We do carpet, tile & grout, upholstery, hard floors, and stain & pet odor removal. We treat our customers like family and strive to achieve outstanding results with every job.

```html
<!DOCTYPE html>
<html lang="en">
<head>
<meta charset="utf-8">
<title>Larkspur Floor Care – Business Card</title>
<link href="https://fonts.googleapis.com/css2?family=Open+Sans:wght@400;600;700;800&display=swap" rel="stylesheet">
<style>
  :root{
    --bg:#e6e6e6;
    --card:#ffffff;
    --ink:#1d1d1b;
    --text:#2b2b2b;
    --blue:#1b7fc4;
    --red:#ee4540;
    --red-deep:#e23c37;
  }
  *{margin:0;padding:0;box-sizing:border-box}
  html,body{width:1200px;height:588px;overflow:hidden;background:var(--bg);font-family:"Open Sans",sans-serif}
  .stage{position:relative;width:1200px;height:588px}
  .card{position:absolute;width:488px;height:289px;background:var(--card);border-radius:20px;overflow:hidden;box-shadow:0 10px 22px rgba(0,0,0,.18)}
  .card--front{left:87px;top:141px}
  .card--back{left:622px;top:142px}

  /* brand: plain square + name in one colour, one weight, one size */
  .brand{position:absolute;display:flex;align-items:center;color:var(--ink);font-weight:700}
  .brand__mark{background:var(--red);flex:none}
  .brand__name{line-height:1.1}
  .card--front .brand{left:80px;top:92px;gap:24px}
  .card--front .brand__mark{width:110px;height:110px}
  .card--front .brand__name{font-size:38px}
  .card--back .brand{left:19px;top:34px;gap:12px}
  .card--back .brand__mark{width:56px;height:56px}
  .card--back .brand__name{font-size:19px}

  /* person */
  .accent-bar{position:absolute;left:0;top:133px;width:13px;height:29px;background:var(--red)}
  .person{position:absolute;left:21px;top:126px}
  .person__name{font-size:18.5px;font-weight:700;line-height:1.2}
  .person__name .first{color:var(--blue)}
  .person__name .last{color:var(--red)}
  .person__role{font-size:12.5px;color:var(--text);margin-top:1px}

  .contacts{position:absolute;left:21px;top:174px;list-style:none;font-size:13px;color:var(--text)}
  .contacts li{display:flex;align-items:center;gap:5px;height:17.5px}
  .contacts svg{width:11px;height:11px;fill:var(--blue);flex:none}
  .address{position:absolute;left:21px;top:236px;font-size:13px;line-height:17.5px;color:var(--text);font-style:normal}

  .mascot-area{position:absolute;right:0;top:0;width:242px;height:289px}
</style>
</head>
<body>
<main class="stage">

  <section class="card card--front" aria-label="Card front">
    <div class="brand">
      <span class="brand__mark"></span>
      <p class="brand__name">Larkspur<br>Floor Care</p>
    </div>
  </section>

  <section class="card card--back" aria-label="Card back">
    <div class="brand">
      <span class="brand__mark"></span>
      <p class="brand__name">Larkspur<br>Floor Care</p>
    </div>

    <span class="accent-bar"></span>
    <div class="person">
      <p class="person__name"><span class="first">Marla</span> <span class="last">Quintero</span></p>
      <p class="person__role">Executive Director</p>
    </div>

    <ul class="contacts">
      <li><svg viewBox="0 0 24 24"><path d="M6.6 10.8c1.4 2.8 3.8 5.1 6.6 6.6l2.2-2.2c.3-.3.7-.4 1-.2 1.1.4 2.3.6 3.6.6.6 0 1 .4 1 1V20c0 .6-.4 1-1 1C10.6 21 3 13.4 3 4c0-.6.4-1 1-1h3.5c.6 0 1 .4 1 1 0 1.3.2 2.5.6 3.6.1.3 0 .7-.2 1z"/></svg>555 204 8817</li>
      <li><svg viewBox="0 0 24 24"><path d="M3 5h18c.6 0 1 .4 1 1v.5l-10 6-10-6V6c0-.6.4-1 1-1zm-1 4 10 6 10-6v9c0 .6-.4 1-1 1H3c-.6 0-1-.4-1-1z"/></svg>hello@larkspurfloor.com</li>
      <li><svg viewBox="0 0 24 24"><path d="M12 2a10 10 0 1 0 0 20 10 10 0 0 0 0-20zm6.9 6h-3a15 15 0 0 0-1.3-4A8 8 0 0 1 18.9 8zM12 4c.8 1.2 1.5 2.5 1.9 4h-3.8c.4-1.5 1.1-2.8 1.9-4zM4.3 14a8 8 0 0 1 0-4h3.4a16 16 0 0 0 0 4zm.8 2h3a15 15 0 0 0 1.3 4A8 8 0 0 1 5.1 16zm3-8h-3a8 8 0 0 1 4.3-4 15 15 0 0 0-1.3 4zM12 20c-.8-1.2-1.5-2.5-1.9-4h3.8c-.4 1.5-1.1 2.8-1.9 4zm2.3-6H9.7a14 14 0 0 1 0-4h4.6a14 14 0 0 1 0 4zm.3 6a15 15 0 0 0 1.3-4h3a8 8 0 0 1-4.3 4zm1.7-6a16 16 0 0 0 0-4h3.4a8 8 0 0 1 0 4z"/></svg>www.larkspurfloor.com</li>
    </ul>

    <address class="address">2270 Harbor Lane<br>Lake Orrin,</address>

    <svg class="mascot-area" viewBox="0 0 242 289" role="img" aria-label="Cartoon mascot of a cleaning technician in a blue cap and shirt raising a steam wand, standing before a red burst panel">
      <polygon points="0,211 242,137 242,289 0,289" fill="var(--red-deep)"/>
    </svg>
  </section>

</main>
</body>
</html>
```